Oral Surgeon Referral Pads

Hello. We need referral pads for Dr Elsabet Quorvane, DDS board certified oral surgeon's new office - Harrowgate Dunmere Oral & Maxillofacial Surgery. See logo uploaded. See some images we would like included
Updates

Designs look the same

Font styles to use
Serif
Script

Colors
00AB8E
00BBA5
67D7C9
C6EFE9
E9F9F6

Requirements
Must have
• Color Pantone 623c. Also foldable business cards

```html
<!DOCTYPE html>
<html lang="en">
<head>
<meta charset="utf-8">
<title>Harrowgate Dunmere Oral &amp; Maxillofacial Surgery – Referral Pad</title>
<link href="https://fonts.googleapis.com/css2?family=Lora:wght@400;600&family=Great+Vibes&display=swap" rel="stylesheet">
<style>
  :root {
    --teal-deep: #00ab8e;
    --teal: #00bba5;
    --teal-soft: #67d7c9;
    --teal-pale: #c6efe9;
    --teal-mist: #e9f9f6;
    --ink: #24403b;
    --paper: #ffffff;
    --backdrop: #e6e6e6;
  }
  * { margin: 0; padding: 0; box-sizing: border-box; }
  html, body { width: 1200px; height: 1200px; overflow: hidden; background: var(--backdrop); }
  body { font-family: "Lora", Georgia, serif; color: var(--ink); position: relative; }

  .pad {
    position: absolute; left: 187px; top: 22px;
    width: 1046px; height: 1464px; background: var(--paper);
    transform: scale(0.79); transform-origin: top left;
  }

  /* brand */
  .brand { position: absolute; left: 40px; top: 56px; width: 344px; text-align: center; color: var(--teal-deep); font-weight: 600; }
  .brand-mark { width: 70px; height: 70px; border-radius: 50%; background: var(--teal-mist); border: 2px solid var(--teal-soft); margin: 0 auto 16px; }
  .brand-name { font-size: 30px; line-height: 1.25; }
  .brand-sub { font-size: 18px; line-height: 1.5; }

  /* contact */
  .contact { position: absolute; left: 676px; top: 36px; }
  .contact-row { display: flex; align-items: center; height: 27.5px; font-size: 18px; }
  .contact-row svg { width: 16px; height: 16px; margin-right: 7px; fill: var(--teal-deep); flex: none; }

  /* referral band */
  .referral-band { position: absolute; left: 59px; top: 225px; width: 930px; height: 152px; }
  .band-row { position: absolute; left: 0; width: 100%; height: 73px; background: var(--teal-deep); color: #fff; font-size: 19px; letter-spacing: 0.5px; }
  .band-row.top { top: 0; border-radius: 38px 38px 0 0; }
  .band-row.bottom { top: 79px; border-radius: 0 0 38px 38px; background: var(--teal); }
  .band-label { position: absolute; top: 23px; }
  .band-label.left { left: 45px; }
  .band-label.right { left: 620px; }

  /* framed sections */
  .frame { position: absolute; left: 60px; width: 927px; border: 2px solid var(--teal); border-radius: 30px; background: var(--teal-mist); }
  .frame-tab { position: absolute; left: 380px; width: 287px; height: 47px; background: var(--teal-deep); color: #fff; text-align: center; line-height: 47px; }
  .evaluate { top: 434px; height: 301px; }
  .evaluate-tab { top: 411px; font-family: "Great Vibes", cursive; font-size: 34px; }
  .comments { top: 1196px; height: 221px; }
  .comments-tab { top: 1173px; font-size: 24px; letter-spacing: 1px; }

  .checklist { position: absolute; top: 478px; list-style: none; font-size: 18.5px; }
  .checklist li { height: 31.4px; display: flex; align-items: center; white-space: nowrap; }
  .checklist li::before { content: ""; width: 15px; height: 15px; border: 1.6px solid var(--teal-deep); background: #fff; border-radius: 2px; margin-right: 9px; flex: none; }
  .col-1 { left: 86px; }
  .col-2 { left: 386px; }
  .col-3 { left: 684px; }

  /* tooth chart */
  .tooth { position: absolute; transform: translateX(-50%); font-size: 22px; line-height: 30px; white-space: nowrap; }
  .chart-rule { position: absolute; left: 58px; top: 845px; width: 931px; height: 2px; background: var(--teal-deep); }
  .chart-divider { position: absolute; left: 533px; top: 774px; width: 2px; height: 142px; background: var(--teal-deep); }

  /* note */
  .note { position: absolute; left: 68px; top: 955px; width: 912px; font-size: 21px; line-height: 38px; }

  .write-line { position: absolute; left: 100px; width: 846px; height: 2px; background: var(--teal); }
</style>
</head>
<body>
<div class="pad">

  <div class="brand">
    <div class="brand-mark"></div>
    <div class="brand-name">Harrowgate Dunmere</div>
    <div class="brand-sub">Oral &amp; Maxillofacial Surgery</div>
  </div>

  <div class="contact">
    <div class="contact-row"><svg viewBox="0 0 16 16"><path d="M8 0a5.5 5.5 0 0 0-5.5 5.5C2.5 10 8 16 8 16s5.5-6 5.5-10.5A5.5 5.5 0 0 0 8 0zm0 8a2.5 2.5 0 1 1 0-5 2.5 2.5 0 0 1 0 5z"/></svg>Your address, City State, Zip 1234</div>
    <div class="contact-row"><svg viewBox="0 0 16 16"><path d="M3.6 1.2l2.2 2.9-1.3 1.6c.9 2 2.4 3.6 4.4 4.6l1.6-1.3 2.9 2.2-1.4 2.6C6.6 13.6 2.4 9.4 1 3.2z"/></svg>123 456 789</div>
    <div class="contact-row"><svg viewBox="0 0 16 16"><path d="M1 4h3v11H1zM5 2h9v13H5zm2 2v3h5V4zm0 5v1.5h1.5V9zm3 0v1.5h1.5V9zm-3 3v1.5h1.5V12zm3 0v1.5h1.5V12z"/></svg>123 456 789</div>
    <div class="contact-row"><svg viewBox="0 0 16 16"><path d="M1 6l7-5 7 5v9H1zm2 1v.5l5 3.5 5-3.5V7L8 3.5z"/></svg>info@harrowgatedunmere.com</div>
    <div class="contact-row"><svg viewBox="0 0 16 16"><path d="M8 0a8 8 0 1 0 0 16A8 8 0 0 0 8 0zm1 14.9V12l2-2-2-2H6L4 6V3.2A6.9 6.9 0 0 1 14.9 8 7 7 0 0 1 9 14.9z"/></svg>www.harrowgatedunmere.com</div>
  </div>

  <div class="referral-band">
    <div class="band-row top">
      <span class="band-label left">INTRODUCING</span>
      <span class="band-label right">DATE</span>
    </div>
    <div class="band-row bottom">
      <span class="band-label left">REFFERRED BY</span>
      <span class="band-label right">PHONE</span>
    </div>
  </div>

  <div class="frame evaluate"></div>
  <div class="frame-tab evaluate-tab">Evaluate/Treat</div>

  <ul class="checklist col-1">
    <li>Wisdom Teeth</li><li>Extraction</li><li>Implants</li><li>Bone Grafing</li>
    <li>Exposure and bonding</li><li>Biopsy(SOFT or Hard Tissue)</li><li>Connectivee Tissue Graft</li>
  </ul>
  <ul class="checklist col-2">
    <li>Wisdom Teeth</li><li>Extraction</li><li>Implants</li><li>Bone Grafing</li>
    <li>Exposure and bonding</li><li>Biopsy(SOFT or Hard Tissue)</li><li>Connectivee Tissue Graft</li>
  </ul>
  <ul class="checklist col-3">
    <li>Wisdom Teeth</li><li>Extraction</li><li>Implants</li><li>Bone Grafing</li>
    <li>Exposure and bonding</li><li>Biopsy(SOFT or Hard Tissue)</li><li>Connectivee Tissue Graft</li>
  </ul>

  <!-- tooth chart: upper numbers -->
  <span class="tooth" style="left:127px;top:769px">1</span>
  <span class="tooth" style="left:172px;top:769px">2</span>
  <span class="tooth" style="left:219px;top:769px">3</span>
  <span class="tooth" style="left:268px;top:769px">4</span>
  <span class="tooth" style="left:317px;top:769px">5</span>
  <span class="tooth" style="left:365px;top:769px">6</span>
  <span class="tooth" style="left:413px;top:769px">7</span>
  <span class="tooth" style="left:461px;top:769px">8</span>
  <span class="tooth" style="left:508px;top:769px">9</span>
  <span class="tooth" style="left:562px;top:769px">10</span>
  <span class="tooth" style="left:621px;top:769px">11</span>
  <span class="tooth" style="left:679px;top:769px">12</span>
  <span class="tooth" style="left:739px;top:769px">13</span>
  <span class="tooth" style="left:799px;top:769px">14</span>
  <span class="tooth" style="left:860px;top:769px">15</span>
  <span class="tooth" style="left:920px;top:769px">16</span>
  <!-- upper letters -->
  <span class="tooth" style="left:317px;top:807px">A</span>
  <span class="tooth" style="left:365px;top:807px">B</span>
  <span class="tooth" style="left:413px;top:807px">C</span>
  <span class="tooth" style="left:461px;top:807px">D</span>
  <span class="tooth" style="left:508px;top:807px">E</span>
  <span class="tooth" style="left:562px;top:807px">F</span>
  <span class="tooth" style="left:621px;top:807px">G</span>
  <span class="tooth" style="left:679px;top:807px">H</span>
  <span class="tooth" style="left:739px;top:807px">I</span>

  <div class="chart-rule"></div>
  <div class="chart-divider"></div>

  <!-- lower letters -->
  <span class="tooth" style="left:317px;top:855px">T</span>
  <span class="tooth" style="left:365px;top:855px">S</span>
  <span class="tooth" style="left:413px;top:855px">R</span>
  <span class="tooth" style="left:461px;top:855px">Q</span>
  <span class="tooth" style="left:508px;top:855px">P</span>
  <span class="tooth" style="left:562px;top:855px">O</span>
  <span class="tooth" style="left:621px;top:855px">N</span>
  <span class="tooth" style="left:679px;top:855px">M</span>
  <span class="tooth" style="left:739px;top:855px">L</span>
  <span class="tooth" style="left:799px;top:855px">14</span>
  <span class="tooth" style="left:860px;top:855px">15</span>
  <span class="tooth" style="left:920px;top:855px">16</span>
  <!-- lower numbers -->
  <span class="tooth" style="left:127px;top:894px">32</span>
  <span class="tooth" style="left:174px;top:894px">31</span>
  <span class="tooth" style="left:220px;top:894px">30</span>
  <span class="tooth" style="left:269px;top:894px">29</span>
  <span class="tooth" style="left:317px;top:894px">28</span>
  <span class="tooth" style="left:365px;top:894px">27</span>
  <span class="tooth" style="left:413px;top:894px">26</span>
  <span class="tooth" style="left:461px;top:894px">25</span>
  <span class="tooth" style="left:508px;top:894px">24</span>
  <span class="tooth" style="left:563px;top:894px">23</span>
  <span class="tooth" style="left:621px;top:894px">22</span>
  <span class="tooth" style="left:681px;top:894px">21</span>
  <span class="tooth" style="left:739px;top:894px">20</span>
  <span class="tooth" style="left:799px;top:894px">19</span>
  <span class="tooth" style="left:860px;top:894px">18</span>
  <span class="tooth" style="left:920px;top:894px">17</span>

  <p class="note">Lorem Ipsum is simply dummy text of the printing and typesetting industry. Lorem Ipsum has been the industry's standard dummy text ever since the 1500s, when an unknown printer took a galley of type and scrambled it to make a type specimen book. It has survived not only five centuries, but also the leap into electronic typesetting, remaining essentially unchanged. It was popularised in the 1960s with the</p>

  <div class="frame comments"></div>
  <div class="frame-tab comments-tab">COMMENTS</div>
  <div class="write-line" style="top:1267px"></div>
  <div class="write-line" style="top:1321px"></div>
  <div class="write-line" style="top:1375px"></div>

</div>
</body>
</html>
```